Im open to ideas.. I was thinking on my business cards aswell as my logo. a place for my name. email. phone number and abn..

ive attched a file with my business logo. which i dont love the colours.. i was think a dark background with charcoal letters so something along those colour schumes but im open to ideas..

BRM Constructions

```html
<!DOCTYPE html>
<html lang="en">
<head>
<meta charset="utf-8">
<title>BRM Constructions – Business Cards</title>
<link rel="stylesheet" href="https://fonts.googleapis.com/css2?family=Source+Sans+3:wght@400;600;700&display=swap">
<style>
  :root {
    --charcoal: #272425;
    --red: #e31b23;
    --white: #ffffff;
    --grey-text: #d9d6d6;
    --backdrop: #ecebe9;
  }
  * { margin: 0; padding: 0; box-sizing: border-box; }
  html, body {
    width: 1200px;
    height: 900px;
    overflow: hidden;
    background: var(--backdrop);
    font-family: "Source Sans 3", "Helvetica Neue", Arial, sans-serif;
  }
  .card {
    position: absolute;
    width: 555px;
    height: 342px;
    background: var(--charcoal);
    overflow: hidden;
    box-shadow: 0 6px 18px rgba(0,0,0,0.18);
  }
  .card--front { left: 238px; top: 62px; }
  .card--back { left: 460px; top: 518px; }

  .card__shapes { position: absolute; inset: 0; }

  .holder { position: absolute; left: 29px; top: 42px; }
  .holder__name {
    color: var(--red);
    font-weight: 700;
    font-size: 19px;
    line-height: 1.1;
  }
  .holder__title {
    color: var(--grey-text);
    font-size: 15px;
    font-weight: 400;
    margin-top: 2px;
  }

  .abn {
    position: absolute;
    left: 212px;
    top: 131px;
    font-size: 15px;
    color: var(--grey-text);
  }
  .abn__label { color: var(--red); font-weight: 600; }

  .contact-list {
    position: absolute;
    left: 342px;
    top: 188px;
    list-style: none;
  }
  .contact-list__item {
    display: flex;
    align-items: center;
    gap: 8px;
    font-size: 15px;
    color: var(--grey-text);
    height: 20px;
  }
  .contact-list__icon { width: 12px; height: 12px; flex: none; }

  .brand-name {
    position: absolute;
    font-weight: 700;
    white-space: nowrap;
    letter-spacing: 0.3px;
    line-height: 1;
  }
  .brand-name--front {
    left: 26px;
    top: 236px;
    width: 262px;
    font-size: 28px;
    color: var(--charcoal);
  }
  .brand-name--back {
    left: 0;
    right: 0;
    top: 154px;
    text-align: center;
    font-size: 36px;
    color: var(--white);
  }
</style>
</head>
<body>

<section class="card card--front" aria-label="Business card front">
  <svg class="card__shapes" viewBox="0 0 555 342" width="555" height="342" aria-hidden="true">
    <polygon points="0,113 202,113 202,175 319,175 319,276 555,276 555,330 0,330" fill="var(--red)"/>
    <polyline points="0,113 202,113 202,175 319,175 319,276 555,276" fill="none" stroke="var(--white)" stroke-width="3"/>
    <rect x="0" y="330" width="555" height="12" fill="var(--charcoal)"/>
    <polygon points="0,330 0,328 60,300 92,330" fill="var(--charcoal)"/>
  </svg>

  <div class="holder">
    <p class="holder__name">Marcus Hale</p>
    <p class="holder__title">Managing Director</p>
  </div>

  <p class="abn"><span class="abn__label">ABN :</span> 12345678</p>

  <ul class="contact-list">
    <li class="contact-list__item">
      <svg class="contact-list__icon" viewBox="0 0 12 12" aria-hidden="true"><path d="M2.5 0.8 L4.5 3.2 L3.4 4.6 C4.1 6 5.6 7.6 7.2 8.4 L8.6 7.4 L11 9.4 L9.6 11.2 C5.4 10.8 1.2 6.6 0.8 2.2 Z" fill="var(--red)"/></svg>
      <span>044-987 654 321</span>
    </li>
    <li class="contact-list__item">
      <svg class="contact-list__icon" viewBox="0 0 12 12" aria-hidden="true"><rect x="1" y="2.5" width="10" height="7" fill="var(--red)"/><polyline points="1,2.5 6,6.5 11,2.5" fill="none" stroke="var(--charcoal)" stroke-width="1"/></svg>
      <span>info@brmbuild.com</span>
    </li>
    <li class="contact-list__item">
      <svg class="contact-list__icon" viewBox="0 0 12 12" aria-hidden="true"><circle cx="6" cy="6" r="5.2" fill="var(--red)"/><path d="M3 4 L5 3.5 L6 5 L4.5 6.5 Z M7 6.5 L9 7 L8 9.5 Z" fill="var(--charcoal)"/></svg>
      <span>www.brmbuild.com</span>
    </li>
  </ul>

  <p class="brand-name brand-name--front">BRM Constructions</p>
</section>

<section class="card card--back" aria-label="Business card back">
  <p class="brand-name brand-name--back">BRM Constructions</p>
</section>

</body>
</html>
```